Mental Health care Company in Washington DC

We are a new mental health care services provider in Washington DC. Please look at these sites.
https://brightwaterfamilysupport.com
https://www.quietharborinc.com
https://willowgate-dc.org/
https://www.tidepathdc.com
https://www.thelanternofdc.com

```html
<!DOCTYPE html>
<html lang="en">
<head>
<meta charset="utf-8">
<title>Nova Health – Mental Wellness in Washington DC</title>
<link rel="stylesheet" href="https://fonts.googleapis.com/css2?family=Poppins:wght@300;400;500;600;700&family=Dancing+Script:wght@600&display=swap">
<style>
:root{
  --navy:#0f2444;
  --navy-2:#16305a;
  --orange:#f47c20;
  --teal:#4bbfc8;
  --teal-pale:#eef8f9;
  --ink:#1c1f26;
  --muted:#555b66;
  --white:#ffffff;
}
*{box-sizing:border-box;margin:0;padding:0}
html,body{width:1200px;height:4024px;overflow:hidden}
body{position:relative;font-family:'Poppins',sans-serif;color:var(--ink);background:var(--white)}
.abs{position:absolute}
a{color:inherit;text-decoration:none}

/* top bar + header */
.topbar{left:470px;top:0;width:730px;height:31px;background:var(--navy);clip-path:polygon(24px 0,100% 0,100% 100%,0 100%)}
.topbar-edge{left:462px;top:0;width:40px;height:31px;background:var(--orange);clip-path:polygon(12px 0,32px 0,20px 100%,0 100%)}
.topbar-info{left:548px;top:0;height:31px;display:flex;gap:28px;align-items:center;font-size:10px;color:#cfd6e2}
.topbar-info span b{color:#fff;font-weight:500}
.topbar-info svg{vertical-align:-2px;margin-right:4px}
.brand{left:92px;top:36px;display:flex;align-items:center;gap:10px}
.brand-dot{width:14px;height:14px;border-radius:50%;background:var(--orange)}
.brand-name{font-size:30px;font-weight:500;color:var(--navy);letter-spacing:-.5px;line-height:1}
.nav{left:553px;top:52px;display:flex;gap:40px;font-size:13px;color:var(--ink)}
.nav .active{color:var(--orange);border-bottom:2px solid var(--orange);padding-bottom:3px}
.btn-contact{left:994px;top:48px;width:108px;height:28px;border-radius:14px;background:var(--orange);color:#fff;font-size:10px;font-weight:600;display:flex;align-items:center;justify-content:center}

/* hero */
.hero-photo{left:0;top:91px;width:1200px;height:530px;background:linear-gradient(100deg,#8b6a5a 0%,#c9c3bc 30%,#e4e6e8 55%,#b9c3cc 80%,#8d99a4 100%)}
.hero-card{left:131px;top:208px;width:496px;height:295px;background:#fff;border-radius:14px;text-align:center;padding-top:33px}
.hero-card h1{font-size:31px;font-weight:400;line-height:45px;color:var(--navy);letter-spacing:.5px}
.hero-card h1 strong{color:var(--orange);font-weight:700}
.hero-card p{font-size:13.5px;color:var(--ink);line-height:22px;margin:17px auto 0;width:420px}
.hero-form{display:flex;margin:28px auto 0;width:429px;height:58px;border-radius:8px;overflow:hidden}
.hero-form span{flex:1;background:#f0f0f0;font-size:12px;font-weight:500;text-align:left;padding-left:22px;line-height:58px}
.hero-form b{width:102px;background:var(--navy);color:#fff;font-size:11px;font-weight:600;line-height:58px}

/* features */
.feature{top:688px;display:flex;gap:22px;width:300px}
.feature-icon{flex:none;width:62px;height:62px;border-radius:50%;border:1.5px solid #e7d6c8;display:flex;align-items:center;justify-content:center}
.feature h3{font-size:14px;font-weight:500;margin-top:3px}
.feature p{font-size:11px;color:var(--muted);line-height:19px;margin-top:9px;width:215px}
.divider{left:103px;top:840px;width:994px;height:1px;background:#cfd3d8}

/* question banner */
.ask{left:141px;top:912px;width:917px;height:207px;border-radius:18px;overflow:hidden;background:linear-gradient(90deg,#f47c20 0%,#f58a30 45%,#f9b67a 65%,#f4eee8 80%,#dfe3e6 100%)}
.ask-photo{right:0;top:0;width:330px;height:207px;background:linear-gradient(90deg,rgba(240,236,230,0) 0%,#e2e4e6 40%,#c8ccd0 100%)}
.ask-text{left:68px;top:42px;color:#fff}
.ask-text em{font-family:'Dancing Script',cursive;font-style:normal;font-size:22px;color:#ffe27a}
.ask-text h2{font-size:23px;font-weight:500;line-height:34px;margin-top:6px}
.ask-text a{display:inline-block;margin-top:9px;font-size:13px;text-decoration:underline}
.ask-deco{left:1108px;top:1025px;width:92px;height:100px;background:linear-gradient(135deg,#bfe8ef,#f3f5f6);border-radius:8px;opacity:.8}

/* ticker */
.ticker{left:0;top:1206px;width:1200px;height:49px;background:var(--teal);display:flex;align-items:center;white-space:nowrap;overflow:hidden;color:#fff;font-size:15px;font-weight:500}
.ticker span{display:inline-flex;align-items:center;gap:14px;margin-right:24px}
.ticker span:first-child{margin-left:-36px}

/* about */
.about-bg{left:0;top:1255px;width:605px;height:567px;background:var(--teal-pale)}
.about-rule{left:605px;top:1255px;width:1px;height:567px;background:#cfd8dc}
.about-base{left:0;top:1822px;width:1200px;height:1px;background:#cfd8dc}
.about-photo{left:0;top:1341px;width:520px;height:397px;border-radius:0 14px 14px 0;background:linear-gradient(120deg,#c7b8a6 0%,#5fa3c7 45%,#2f7fb3 75%,#1d5d8c 100%)}
.eyebrow{font-size:14px;color:var(--teal);font-weight:500;letter-spacing:.3px;display:flex;align-items:center;gap:10px}
.eyebrow i{display:block;width:60px;height:1px;background:#bfe0e4}
.about-text{left:673px;top:1346px;width:440px}
.about-text h2{font-size:30px;font-weight:600;color:var(--navy);line-height:36px;margin-top:16px}
.about-text p{font-size:12.5px;line-height:22.7px;color:#333;margin-top:21px}
.btn-pill{display:inline-flex;align-items:center;justify-content:center;height:36px;border-radius:18px;background:var(--orange);color:#fff;font-size:12px;font-weight:500;padding:0 31px;margin-top:26px}

/* services */
.services-head{left:0;top:1910px;width:1200px;text-align:center}
.services-head .eyebrow{justify-content:center}
.services-head h2{font-size:30px;font-weight:600;color:var(--navy)}
.svc{top:2031px;width:282px;height:316px;border:1.5px solid #5d6270;text-align:center}
.svc-photo{margin:13px auto 0;width:252px;height:141px}
.svc h3{font-size:16.5px;font-weight:500;margin-top:26px}
.svc p{font-size:12.5px;line-height:23px;color:#333;margin:10px auto 0;width:245px}
.svc-icon{position:absolute;left:50%;bottom:-26px;margin-left:-26px;width:52px;height:52px;border-radius:50%;background:var(--teal);border:4px solid #d8f1f3;display:flex;align-items:center;justify-content:center}

/* journey */
.journey{left:0;top:2469px;width:1200px;height:401px;background:linear-gradient(90deg,#d6c3ae 0%,#c9a88b 22%,#ef8b3a 45%,#f47c20 60%,#f47c20 100%)}
.journey-text{left:630px;top:2555px;color:#fff}
.journey-text h2{font-size:34px;font-weight:500;line-height:48px}
.journey-text p{font-size:14px;line-height:25px;margin-top:14px;color:#ffe9d6;width:400px}
.btn-ghost{display:inline-flex;align-items:center;justify-content:center;height:38px;border:1.5px solid #fff;border-radius:19px;padding:0 26px;font-size:13px;font-weight:500;margin-top:26px}

/* values strip */
.values{left:-30px;top:2920px;width:1260px;white-space:nowrap;font-size:75px;font-weight:600;letter-spacing:1px;line-height:100px}
.values .outline{color:transparent;-webkit-text-stroke:1.5px #3a3f4a}
.values .solid{color:var(--ink)}

/* testimonials */
.reviews-head{left:0;top:3078px;width:1200px;text-align:center;font-size:30px;font-weight:600;line-height:42px;color:var(--ink)}
.review{top:3208px;width:284px;height:240px;background:#fff;box-shadow:0 2px 14px rgba(20,30,50,.08);padding:16px 22px}
.review .quote{position:absolute;right:18px;top:-22px;width:40px;height:40px;border-radius:50%;background:#fff;display:flex;align-items:center;justify-content:center;font-size:26px;font-weight:700;line-height:1}
.review .avatar{width:60px;height:60px;border-radius:50%;background:linear-gradient(135deg,#cbd2d9,#6f7986)}
.review .stars{position:absolute;left:104px;top:36px;color:var(--orange);font-size:20px;letter-spacing:3px}
.review h4{font-size:13px;font-weight:500;margin-top:14px}
.review p{font-size:11px;line-height:20px;color:#333;margin-top:3px}
.dots{left:558px;top:3468px;display:flex;gap:7px}
.dots i{width:11px;height:11px;border-radius:50%;background:#d6d9dd}
.dots i:first-child{background:var(--orange)}

/* footer */
.footer{left:0;top:3559px;width:1200px;height:465px;background:var(--navy)}
.foot-brand{left:141px;top:3684px;display:flex;align-items:center;gap:10px}
.foot-brand .brand-name{color:#fff}
.foot-about{left:138px;top:3744px;width:200px;font-size:12px;line-height:22px;color:#e4e8ef}
.foot-col h4{font-size:16px;font-weight:600;color:var(--orange)}
.foot-links{list-style:none;margin-top:20px;font-size:12px;color:#e4e8ef}
.foot-links li{margin-bottom:14px}
.foot-links li::before{content:"• ";}
.foot-info{font-size:12px;line-height:22px;color:#e4e8ef}
.foot-info b{display:block;color:var(--orange);font-weight:500;margin-top:16px}
.stay{left:781px;top:3644px;width:291px;height:254px;border-radius:12px;background:var(--navy-2);padding:30px 37px}
.stay p{font-size:12px;line-height:22px;color:#e4e8ef;margin-top:14px}
.stay-input{margin-top:20px;height:38px;border-radius:19px;background:#fff;font-size:11.5px;color:#666;padding:0 20px;display:flex;align-items:center;justify-content:space-between}
.stay-btn{margin-top:14px;width:152px;height:36px;border-radius:18px;background:var(--orange);color:#fff;font-size:12px;display:flex;align-items:center;justify-content:space-between;padding:0 20px 0 22px}
.foot-rule{left:141px;top:3969px;width:918px;height:1px;background:#2f4468}
.foot-bottom{left:141px;top:3988px;width:918px;display:flex;justify-content:space-between;font-size:12px;color:#e4e8ef}
</style>
</head>
<body>

<!-- header -->
<div class="abs topbar-edge"></div>
<div class="abs topbar"></div>
<div class="abs topbar-info">
  <span><svg width="11" height="11" viewBox="0 0 24 24"><path fill="#f47c20" d="M6.6 10.8a15 15 0 0 0 6.6 6.6l2.2-2.2c.3-.3.7-.4 1-.2 1.1.4 2.3.6 3.6.6.6 0 1 .4 1 1V20c0 .6-.4 1-1 1A17 17 0 0 1 3 4c0-.6.4-1 1-1h3.5c.6 0 1 .4 1 1 0 1.3.2 2.5.6 3.6.1.3 0 .7-.2 1z"/></svg>Call now: <b>(555) 014-2280</b></span>
  <span><svg width="12" height="10" viewBox="0 0 24 18"><rect width="24" height="18" rx="2" fill="#f47c20"/><path d="M1 2l11 8 11-8" stroke="#0f2444" stroke-width="2" fill="none"/></svg>Email: <b>hello@novamind.example</b></span>
  <span><svg width="11" height="11" viewBox="0 0 24 24"><circle cx="12" cy="12" r="11" fill="#f47c20"/><path d="M12 6v6l4 2" stroke="#0f2444" stroke-width="2" fill="none"/></svg>Time: <b>Mon - Sat, 09:00am to 06:00pm</b></span>
</div>
<div class="abs brand"><span class="brand-dot"></span><span class="brand-name">Nova Health</span></div>
<nav class="abs nav"><a class="active">Home</a><a>About Us</a><a>Services ⌄</a><a>Blog</a><a>FAQs</a></nav>
<a class="abs btn-contact">Contact Now</a>

<!-- hero -->
<div class="abs hero-photo" role="img" aria-label="Photo of a bright clinic corridor with a doctor and nurse walking"></div>
<div class="abs hero-card">
  <h1>MENTAL WELLNESS<br>FOR A <strong>STRONGER YOU</strong></h1>
  <p>Evidence-based care tailored to your needs. Where clinical expertise meets your unique needs</p>
  <div class="hero-form"><span>Enter your email</span><b>Subscribe</b></div>
</div>

<!-- features -->
<div class="abs feature" style="left:141px">
  <div class="feature-icon"><svg width="28" height="28" viewBox="0 0 24 24" fill="none" stroke="#f47c20" stroke-width="1.4"><path d="M12 9.5c-1-2-4-1.6-4 .6 0 1.8 4 4 4 4s4-2.2 4-4c0-2.2-3-2.6-4-.6z"/><path d="M3 17h4l3 2h6l5-3-1-1-4 1"/></svg></div>
  <div><h3>Personalized Family Care</h3><p>We treat you like family, building lasting relationships based on trust and compassion</p></div>
</div>
<div class="abs feature" style="left:451px">
  <div class="feature-icon"><svg width="28" height="28" viewBox="0 0 24 24" fill="none" stroke="#4bbfc8" stroke-width="1.4"><path d="M12 20s-8-4.6-8-10a4.5 4.5 0 0 1 8-2.8A4.5 4.5 0 0 1 20 10c0 5.4-8 10-8 10z"/><path d="M12 9v5M9.5 11.5h5"/></svg></div>
  <div><h3>Comprehensive Services</h3><p>From routine checkups to specialized testing, we offer a wide range of services to meet your needs</p></div>
</div>
<div class="abs feature" style="left:768px">
  <div class="feature-icon"><svg width="28" height="28" viewBox="0 0 24 24" fill="none" stroke="#f47c20" stroke-width="1.4"><rect x="6" y="6" width="12" height="12" rx="3"/><path d="M12 9v6M9 12h6"/><circle cx="12" cy="12" r="9"/></svg></div>
  <div><h3>Experienced &amp; Caring Staff</h3><p>Our team of dedicated professionals is committed to providing the highest quality care</p></div>
</div>
<div class="abs divider"></div>

<!-- question banner -->
<div class="abs ask">
  <div class="abs ask-photo" role="img" aria-label="Photo of a doctor's hand holding a stethoscope"></div>
  <div class="abs ask-text">
    <em>Have A Question?</em>
    <h2>Reach out to schedule your appointment or<br>get answers to your questions</h2>
    <a>Schedule an Appointment Today!</a>
  </div>
</div>
<div class="abs ask-deco" role="img" aria-label="Decorative capsules and syringe"></div>

<!-- ticker -->
<div class="abs ticker">
  <span>Private Care <svg width="20" height="18" viewBox="0 0 24 22" fill="none" stroke="#fff" stroke-width="2"><path d="M12 20S2 14 2 7.5A5 5 0 0 1 12 5a5 5 0 0 1 10 2.5C22 14 12 20 12 20z"/></svg></span>
  <span>Family-Focused <svg width="20" height="18" viewBox="0 0 24 22" fill="none" stroke="#fff" stroke-width="2"><path d="M12 20S2 14 2 7.5A5 5 0 0 1 12 5a5 5 0 0 1 10 2.5C22 14 12 20 12 20z"/></svg></span>
  <span>Comprehensive Services <svg width="20" height="18" viewBox="0 0 24 22" fill="none" stroke="#fff" stroke-width="2"><path d="M12 20S2 14 2 7.5A5 5 0 0 1 12 5a5 5 0 0 1 10 2.5C22 14 12 20 12 20z"/></svg></span>
  <span>Advanced Testing <svg width="20" height="18" viewBox="0 0 24 22" fill="none" stroke="#fff" stroke-width="2"><path d="M12 20S2 14 2 7.5A5 5 0 0 1 12 5a5 5 0 0 1 10 2.5C22 14 12 20 12 20z"/></svg></span>
  <span>Community Health <svg width="20" height="18" viewBox="0 0 24 22" fill="none" stroke="#fff" stroke-width="2"><path d="M12 20S2 14 2 7.5A5 5 0 0 1 12 5a5 5 0 0 1 10 2.5C22 14 12 20 12 20z"/></svg></span>
  <span>Personalized Healthcare <svg width="20" height="18" viewBox="0 0 24 22" fill="none" stroke="#fff" stroke-width="2"><path d="M12 20S2 14 2 7.5A5 5 0 0 1 12 5a5 5 0 0 1 10 2.5C22 14 12 20 12 20z"/></svg></span>
  <span>Comprehensive Services</span>
</div>

<!-- about -->
<div class="abs about-bg"></div>
<div class="abs about-rule"></div>
<div class="abs about-base"></div>
<div class="abs about-photo" role="img" aria-label="Photo of a father and son giving a high five to a smiling nurse"></div>
<div class="abs about-text">
  <div class="eyebrow">WHO WE ARE <svg width="16" height="16" viewBox="0 0 16 16"><path d="M8 1v6M8 9v6M1 8h6M9 8h6" stroke="#f47c20" stroke-width="2"/><circle cx="8" cy="8" r="1.5" fill="#4bbfc8"/></svg><i></i></div>
  <h2>A Trusted Mental Health<br>Partner In DC</h2>
  <p>Lorem Ipsum is simply dummy text of the printing and typesetting industry. Lorem Ipsum has been the industry's standard dummy text ever since the 1500s, when an unknown printer took a galley of type and scrambled it to make a type specimen book. It has survived not only five centuries, but also the leap into electronic typesetting, remaining essentially unchanged. It was popularised in the 1960s with the release of Quillmark sheets containing Lorem Ipsum passages, and more recently with desktop publishing software like Pagewright Studio including versions of Lorem Ipsum</p>
  <a class="btn-pill">Learn More About Us</a>
</div>

<!-- services -->
<div class="abs services-head">
  <div class="eyebrow">OUR CORE SERVICES</div>
  <svg width="120" height="16" viewBox="0 0 120 16" style="margin-top:8px"><path d="M0 8h50M70 8h50" stroke="#bfe0e4"/><path d="M60 1v6M60 9v6M53 8h6M61 8h6" stroke="#f47c20" stroke-width="2"/></svg>
  <h2 style="margin-top:6px">Transformative Services For Real Results</h2>
</div>
<div class="abs svc" style="left:141px">
  <div class="svc-photo" role="img" aria-label="Photo of a therapist comforting a young woman on a sofa" style="background:linear-gradient(120deg,#e8dfd6,#c9b6a4)"></div>
  <h3>Individual Therapy</h3>
  <p>Lorem Ipsum is simply dummy text of the printing and typesetting industry. Lorem Ipsum has been the.</p>
  <div class="svc-icon"><svg width="22" height="22" viewBox="0 0 24 24" fill="none" stroke="#fff" stroke-width="1.6"><path d="M8 20v-4a7 7 0 1 1 8 0v4"/><path d="M12 8v5M9.5 10.5h5"/></svg></div>
</div>
<div class="abs svc" style="left:459px">
  <div class="svc-photo" role="img" aria-label="Photo of a group of medical professionals standing together" style="background:linear-gradient(120deg,#dfe4ea,#8795a5)"></div>
  <h3>Support Groups</h3>
  <p>Lorem Ipsum is simply dummy text of the printing and typesetting industry. Lorem Ipsum has been the.</p>
  <div class="svc-icon"><svg width="22" height="22" viewBox="0 0 24 24" fill="none" stroke="#fff" stroke-width="1.6"><circle cx="8" cy="7" r="3"/><circle cx="16" cy="7" r="3"/><path d="M3 20v-2a5 5 0 0 1 10 0v2M11 20v-2a5 5 0 0 1 10 0v2"/></svg></div>
</div>
<div class="abs svc" style="left:778px">
  <div class="svc-photo" role="img" aria-label="Photo of a doctor consulting with an older patient" style="background:linear-gradient(120deg,#2c4d7a,#6f9fc8)"></div>
  <h3>Counseling</h3>
  <p>Lorem Ipsum is simply dummy text of the printing and typesetting industry. Lorem Ipsum has been the.</p>
  <div class="svc-icon"><svg width="22" height="22" viewBox="0 0 24 24" fill="none" stroke="#fff" stroke-width="1.6"><rect x="3" y="4" width="18" height="13" rx="2"/><path d="M7 9h10M7 12h7M8 17l-2 4 5-4"/></svg></div>
</div>

<!-- journey -->
<div class="abs journey" role="img" aria-label="Photo of a smiling patient and a clinician reviewing notes on a clipboard"></div>
<div class="abs journey-text">
  <h2>Ready To Begin<br>Your Journey To Wellness?</h2>
  <p>Get started on the path to health through the quality medical care our team provides!</p>
  <a class="btn-ghost">Schedule Your Appointment</a>
</div>

<!-- values strip -->
<div class="abs values"><span class="outline">Trustworthy_ </span><span class="solid">Caring_ </span><span class="outline">Professional</span></div>

<!-- testimonials -->
<div class="abs reviews-head">What Our Clients Are Saying – Real Success Stories<br>from Trusted Partners</div>

<div class="abs review" style="left:-159px">
  <div class="quote" style="color:#4bbfc8">❞</div>
  <div class="avatar" role="img" aria-label="Client portrait"></div>
  <div class="stars">★★★☆☆</div>
  <h4>Nina Brandt</h4>
  <p>Lorem Ipsum is simply dummy text of the printing and typesetting industry. Lorem Ipsum has been the industry's standard dummy text ever since the 1500s, when an unknown printer took a galley of type.</p>
</div>
<div class="abs review" style="left:150px">
  <div class="quote" style="color:#f47c20">❞</div>
  <div class="avatar" role="img" aria-label="Client portrait"></div>
  <div class="stars">★★★☆☆</div>
  <h4>Leo Marsh</h4>
  <p>Lorem Ipsum is simply dummy text of the printing and typesetting industry. Lorem Ipsum has been the industry's standard dummy text ever since the 1500s.</p>
</div>
<div class="abs review" style="left:458px">
  <div class="quote" style="color:#4bbfc8">❞</div>
  <div class="avatar" role="img" aria-label="Client portrait"></div>
  <div class="stars">★★★☆☆</div>
  <h4>Owen Hale</h4>
  <p>Lorem Ipsum is simply dummy text of the printing and typesetting industry. Lorem Ipsum has been the industry's.</p>
</div>
<div class="abs review" style="left:766px">
  <div class="quote" style="color:#f47c20">❞</div>
  <div class="avatar" role="img" aria-label="Client portrait"></div>
  <div class="stars">★★★☆☆</div>
  <h4>Rina Castell</h4>
  <p>Lorem Ipsum is simply dummy text of the printing and typesetting industry. Lorem Ipsum has been the industry's standard dummy text ever since the 1500s, when an unknown printer took a galley of type.</p>
</div>
<div class="abs review" style="left:1073px">
  <div class="quote" style="color:#4bbfc8">❞</div>
  <div class="avatar" role="img" aria-label="Client portrait"></div>
  <div class="stars">★★★☆☆</div>
  <h4>Mara Voss</h4>
  <p>Lorem Ipsum is simply dummy text of the printing and typesetting industry. Lorem Ipsum has been the industry's standard dummy text ever.</p>
</div>
<div class="abs dots"><i></i><i></i><i></i><i></i><i></i></div>

<!-- footer -->
<footer class="abs footer"></footer>
<div class="abs foot-brand"><span class="brand-dot"></span><span class="brand-name">Nova Health</span></div>
<p class="abs foot-about">Committed to providing expert mental health care in Washington DC, we empower individuals to heal, grow, and thrive</p>
<div class="abs foot-col" style="left:368px;top:3668px">
  <h4>Quick Links</h4>
  <ul class="foot-links"><li>Home</li><li>About Us</li><li>Sevices</li><li>Blog</li><li>FAQs</li><li>Contact Us</li></ul>
</div>
<div class="abs foot-col" style="left:526px;top:3668px;width:230px">
  <h4>Contact Info</h4>
  <div class="foot-info" style="margin-top:10px">820 Linden Row Suite 4, Washington, DC 20009, United States
    <b>Email Address :</b>info@novamind.example
    <b>Phone Number :</b>(555) 014-2280</div>
</div>
<div class="abs stay">
  <h4 style="font-size:16px;font-weight:600;color:var(--orange)">Stay in Touch</h4>
  <p>Stay updated with health tips and exclusive offers!</p>
  <div class="stay-input">Email address <svg width="14" height="11" viewBox="0 0 24 18"><rect width="24" height="18" rx="2" fill="#8a8f98"/><path d="M1 2l11 8 11-8" stroke="#fff" stroke-width="2" fill="none"/></svg></div>
  <div class="stay-btn">Subscribe <svg width="14" height="14" viewBox="0 0 24 24"><path d="M3 3l18 9-18 9 4-9z" fill="#fff"/></svg></div>
</div>
<div class="abs foot-rule"></div>
<div class="abs foot-bottom"><span>Copyright © 2025 Nova Mental Health | All Rights Reserved.</span><span>Terms &amp; Condition &nbsp; | &nbsp; Privacy Policy &nbsp; | &nbsp; Support</span></div>

</body>
</html>
```